Professional and creative business card design for recruiting service providers

Our company supports German medium-sized companies in filling vacancies promptly. For this we use social media marketing and bring our customers into the visibility.

We want a professional but also creative design for our business cards.

Please look at lindqvar-staff.de to get an impression of our CI.

Target Market(s)

Small and medium-sized companies in Germany from the industry

Industry/Entity Type

Industrie, Handwerk

Contact Information for Business Card

Name, Position, Telefonnummer, Email, Website

Colors
EE7325
F08F49
F5BC92
FAE3D3
FDF4ED

Requirements
Must have
• A picture of the employee and in the style of www.lindqvar-staff.de

```html
<!DOCTYPE html>
<html lang="de">
<head>
<meta charset="utf-8">
<title>Lindqvar Staff – Visitenkarte</title>
<link rel="stylesheet" href="https://fonts.googleapis.com/css2?family=Montserrat:wght@800&family=Arimo:wght@400;700&display=swap">
<style>
  :root {
    --orange: #e8582a;
    --ink: #2b2b2d;
    --text: #222226;
    --paper: #ffffff;
    --stage: #e9e9ea;
    --card-dark: #2d2d2f;
    --emboss: #3b3b3e;
    --emboss-light: #47474a;
  }
  * { box-sizing: border-box; margin: 0; padding: 0; }
  html, body { width: 1200px; height: 802px; overflow: hidden; }
  body {
    background: var(--stage);
    font-family: "Arimo", Arial, sans-serif;
    position: relative;
  }
  .card {
    position: absolute;
    top: 236px;
    width: 540px;
    height: 330px;
    border-radius: 4px;
    overflow: hidden;
    box-shadow: 0 10px 28px rgba(0,0,0,.18);
  }
  .card--front { left: 40px; background: var(--paper); }
  .card--back { left: 620px; background: var(--card-dark); }

  .card-art { position: absolute; inset: 0; }

  .brand {
    position: absolute;
    left: 30px;
    top: 36px;
    display: flex;
    align-items: center;
    gap: 14px;
  }
  .brand-square { width: 34px; height: 34px; background: var(--orange); }
  .brand-name {
    font-family: "Montserrat", sans-serif;
    font-weight: 800;
    font-size: 24px;
    line-height: 1.02;
    letter-spacing: 1px;
    color: var(--ink);
  }

  .person { position: absolute; left: 30px; top: 128px; }
  .person-name {
    font-size: 20px;
    font-weight: 400;
    color: var(--orange);
    letter-spacing: .5px;
    text-transform: uppercase;
  }
  .person-role { font-size: 15px; color: var(--text); margin-top: 2px; }

  .contact { position: absolute; left: 30px; top: 196px; font-size: 14px; color: var(--text); line-height: 1.3; }
  .contact-address { margin-bottom: 10px; }
  .contact-line { display: flex; align-items: center; gap: 8px; }
  .contact-line svg { width: 13px; height: 13px; flex: none; }

  .web {
    position: absolute;
    left: 392px;
    top: 280px;
    font-size: 13px;
    color: #fff;
    transform: rotate(-20.8deg);
    transform-origin: center;
    white-space: nowrap;
  }

  .back-brand {
    position: absolute;
    left: 0; right: 0; top: 0; bottom: 0;
    display: flex;
    align-items: center;
    justify-content: center;
    gap: 22px;
  }
  .back-square {
    width: 84px; height: 84px;
    background: var(--emboss);
  }
  .back-name {
    font-family: "Montserrat", sans-serif;
    font-weight: 800;
    font-size: 44px;
    line-height: 1.05;
    letter-spacing: 3px;
    color: var(--emboss-light);
  }
</style>
</head>
<body>

<section class="card card--front">
  <svg class="card-art" viewBox="0 0 540 330" width="540" height="330">
    <defs>
      <linearGradient id="portraitTone" x1="0" y1="0" x2="0" y2="1">
        <stop offset="0" stop-color="#c79a80"/>
        <stop offset=".38" stop-color="#8a6a58"/>
        <stop offset=".55" stop-color="#26262e"/>
        <stop offset="1" stop-color="#1c1c22"/>
      </linearGradient>
    </defs>
    <path role="img" aria-label="Porträtfoto des Mitarbeiters" d="M318 30 H520 V250 L318 318 Z" fill="url(#portraitTone)"/>
    <polygon points="262,330 540,225 540,240 288,330" fill="var(--ink)"/>
    <polygon points="288,330 540,240 540,330" fill="var(--orange)"/>
  </svg>

  <div class="brand">
    <span class="brand-square"></span>
    <span class="brand-name">LINDQVAR<br>STAFF</span>
  </div>

  <div class="person">
    <p class="person-name">Matthias Brenner</p>
    <p class="person-role">Manager</p>
  </div>

  <div class="contact">
    <p class="contact-address">Kastanienallee 27c<br>70182 Stuttgart</p>
    <p class="contact-line">
      <svg viewBox="0 0 24 24"><path d="M6.6 10.8a15 15 0 0 0 6.6 6.6l2.2-2.2c.3-.3.7-.4 1-.2 1.1.4 2.3.6 3.6.6.6 0 1 .4 1 1V20c0 .6-.4 1-1 1A17 17 0 0 1 3 4c0-.6.4-1 1-1h3.5c.6 0 1 .4 1 1 0 1.3.2 2.5.6 3.6.1.3 0 .7-.2 1z" fill="var(--orange)"/></svg>
      0176 204 3915
    </p>
    <p class="contact-line">
      <svg viewBox="0 0 24 24"><rect x="3" y="5" width="18" height="14" rx="1" fill="none" stroke="var(--orange)" stroke-width="2.4"/><path d="M3 6l9 7 9-7" fill="none" stroke="var(--orange)" stroke-width="2.4"/></svg>
      info@lindqvar-staff.de
    </p>
  </div>

  <p class="web">www.lindqvar-staff.de</p>
</section>

<section class="card card--back">
  <div class="back-brand">
    <span class="back-square"></span>
    <span class="back-name">LINDQVAR<br>STAFF</span>
  </div>
</section>

</body>
</html>
```